Real estate broker business card

Want a modern celan but effective business card for my residential and commercial real estate business. I want the back of the card to advertise my services and to capture business. I have attached the back of my current business card fore ideas
Updates

Logos, photo and text updates added! Added Saturday, September 3, 2016

Project Deadline Extended Reason: LOGOS, PHOTOS AND TEST JUST UPLOADED! I'M READY TO PICK A DESIGN! THANK YOU! Added Saturday, September 3, 2016

Target Market(s)

home buyers and seller. commercial buyers and sellers

Industry/Entity Type

Real Estate

Contact Information for Business Card

must have my contact information and my photo

Requirements
Must have
• Carla Ventrino
• Owner & Qualifying Broker
• Ventrino Real Estate Services
• 505.718.2094
• carla@ventrinohomes.example
• www.ventrinohomes.example
Nice to have
• metallic
• Business capture text: " Don't buy or lease property without someone looking out for your best interests. I will represent you on your home or investment purchase for FREE!"
• "Home owners, call today to receive a FREE market analysis for your homes value!

```html
<!DOCTYPE html>
<html lang="en">
<head>
<meta charset="utf-8">
<title>Ventrino Real Estate Services – Business Card</title>
<link rel="stylesheet" href="https://fonts.googleapis.com/css2?family=PT+Sans:wght@400;700&display=swap">
<style>
  :root {
    --backdrop: #141414;
    --card-white: #ffffff;
    --teal: #0e6f7e;
    --teal-light: #1a97a5;
    --teal-deep: #0a5f6d;
    --back-panel: #0b5f6c;
    --ink: #1c1c1c;
    --ink-soft: #3a3a3a;
    --silver: #c9ced1;
  }
  * { box-sizing: border-box; margin: 0; padding: 0; }
  html, body {
    width: 1200px; height: 900px; overflow: hidden;
    background: var(--backdrop);
    font-family: "PT Sans", sans-serif;
  }
  .stage { position: relative; width: 1200px; height: 900px; }
  .card {
    position: absolute; top: 170px; width: 347px; height: 561px;
    box-shadow: 0 4px 14px rgba(0,0,0,.55);
  }
  .card-front { left: 259px; background: var(--card-white); text-align: center; }
  .card-back { left: 631px; background: linear-gradient(180deg, var(--teal-deep), var(--back-panel)); color: #fff; }

  .band {
    position: absolute; left: 102px; width: 143px; height: 30px;
    background: linear-gradient(180deg, var(--teal-light), var(--teal));
  }
  .band-top { top: 0; }
  .band-bottom { bottom: 0; height: 28px; }

  .brand { position: absolute; top: 96px; left: 0; right: 0; color: var(--teal); font-weight: 700; }
  .brand-mark {
    width: 70px; height: 70px; margin: 0 auto 14px;
    border-radius: 50%;
    background: linear-gradient(160deg, var(--silver), var(--teal-light));
  }
  .brand-name { display: block; font-size: 40px; line-height: 40px; letter-spacing: 1px; }
  .brand-sub { display: block; font-size: 14px; letter-spacing: 2.6px; margin-top: 2px; }

  .person { position: absolute; top: 326px; left: 0; right: 0; }
  .person-name { font-size: 22px; font-weight: 700; color: var(--teal); letter-spacing: .5px; line-height: 26px; }
  .person-title { font-size: 15px; color: var(--ink-soft); line-height: 20px; }

  .contact { position: absolute; top: 407px; left: 0; right: 0; font-size: 15px; color: var(--ink); line-height: 21px; }
  .contact-icons { display: flex; justify-content: center; gap: 5px; margin-bottom: 6px; }
  .contact-icons svg { width: 13px; height: 13px; fill: var(--teal); }

  .pitch {
    position: absolute; top: 141px; left: 0; right: 0;
    text-align: center; font-weight: 700; font-size: 19.5px; line-height: 25.2px;
  }
  .pitch p + p { margin-top: 25px; }
</style>
</head>
<body>
<main class="stage">
  <section class="card card-front" aria-label="Card front">
    <div class="band band-top"></div>
    <div class="brand">
      <div class="brand-mark"></div>
      <span class="brand-name">VENTRINO</span>
      <span class="brand-sub">REAL ESTATE SERVICES</span>
    </div>
    <div class="person">
      <h1 class="person-name">CARLA VENTRINO</h1>
      <p class="person-title">Owner &amp; Qualifying Broker</p>
    </div>
    <div class="contact">
      <div class="contact-icons" aria-hidden="true">
        <svg viewBox="0 0 16 16"><path d="M1 6c0-2 3-4 7-4s7 2 7 4v1h-4V5.5C10 5 6 5 5 5.5V7H1zM4 8l2-2h4l2 2 2 6H2z"/></svg>
        <svg viewBox="0 0 16 16"><path d="M1 3h14v10H1z M1.5 3.5 8 9l6.5-5.5" stroke="#fff" stroke-width="1"/></svg>
        <svg viewBox="0 0 16 16"><circle cx="8" cy="8" r="7"/><path d="M5 4c2 1 1 3 3 3s1 3 3 4M4 10l2 1" stroke="#fff" stroke-width="1.2" fill="none"/></svg>
      </div>
      <p class="contact-phone">505.718.2094</p>
      <p class="contact-email">carla@ventrinohomes.example</p>
      <p class="contact-web">www.ventrinohomes.example</p>
    </div>
    <div class="band band-bottom"></div>
  </section>

  <section class="card card-back" aria-label="Card back">
    <div class="pitch">
      <p>Don't buy or lease<br>property without someone<br>looking out for<br>your best interests.<br>I will represent you on<br>your home or<br>investment purchase for FREE!</p>
      <p>Home owners, call today<br>to receive a FREE market analysis<br>for your homes value!</p>
    </div>
  </section>
</main>
</body>
</html>
```